SOLVE Study flyer

I need help designing a flyer for a research study that will include brain imaging in adolescents. The info is in the attached document. The study is called the Sequoia Outlook Lantern Valley Echo (SOLVE) study. Ideally this would be returned as a document that I can edit in the future as we will have several new recruitment phases (different age groups, etc. I also would love to have a logo designed as part of this project, but I recognize that might be a separate design request.

```html
<!DOCTYPE html>
<html lang="en">
<head>
<meta charset="utf-8">
<title>SOLVE Study Flyer</title>
<link href="https://fonts.googleapis.com/css2?family=Montserrat:wght@700;800&family=Fredoka:wght@500;600&family=Poppins:wght@400;500;600&family=Caveat:wght@600;700&family=Varela+Round&display=swap" rel="stylesheet">
<style>
:root{
  --navy:#13214f;
  --purple:#6a3fa0;
  --lavender:#efe6fb;
  --lavender-2:#cdb6ef;
  --yellow:#f7c23a;
  --cream:#fdf5dc;
  --ink:#15193a;
}
*{margin:0;padding:0;box-sizing:border-box}
html,body{width:848px;height:1200px;overflow:hidden;background:#fff}
.flyer{position:relative;width:848px;height:1200px;overflow:hidden;font-family:"Poppins",sans-serif;color:var(--ink);
  background:linear-gradient(180deg,#f4effc 0%,#ffffff 30%,#ffffff 100%)}
.bg-wash{position:absolute;left:0;top:0}
.hero-photo{position:absolute;left:470px;top:55px;width:378px;height:425px;
  background:radial-gradient(ellipse at 60% 35%,#caa98f 0%,#6b4a3a 28%,#b59be0 55%,#d7c5f2 100%);
  border-radius:46% 0 0 30%}
.deco{position:absolute;left:0;top:0;pointer-events:none}
.headline div{position:absolute;white-space:nowrap;line-height:1}
.h-are{left:110px;top:59px;font-family:"Montserrat",sans-serif;font-weight:800;font-size:43px;color:var(--navy)}
.h-parent{left:100px;top:112px;font-family:"Fredoka",sans-serif;font-weight:600;font-size:104px;color:var(--purple);letter-spacing:2px}
.h-child{left:137px;top:206px;font-family:"Montserrat",sans-serif;font-weight:800;font-size:43px;color:var(--navy)}
.h-age{left:120px;top:263px;font-family:"Montserrat",sans-serif;font-weight:800;font-size:48px;color:var(--navy)}
.sub-q{position:absolute;left:68px;top:345px;white-space:nowrap;font-weight:500;font-size:32px;letter-spacing:-1.2px;line-height:1.3;color:var(--navy)}
.sub-q .hand{font-family:"Caveat",cursive;font-weight:700;font-size:46px;line-height:0;color:var(--purple);letter-spacing:0}
.intro-band{position:absolute;left:0;top:455px}
.brain-art{position:absolute;left:105px;top:485px;width:108px;height:104px;border-radius:50%;
  background:radial-gradient(circle,#c6a8ee 0%,#7d5bc0 60%,var(--navy) 100%)}
.intro-text{position:absolute;left:232px;top:487px;width:420px;font-size:19.5px;line-height:28.5px;letter-spacing:-0.7px;color:#fff}
.intro-text strong{color:var(--yellow);font-weight:600}
.panel{position:absolute;border-radius:18px}
.panel-steps{left:60px;top:636px;width:356px;height:354px;background:var(--lavender)}
.panel-elig{left:432px;top:640px;width:366px;height:348px;background:var(--cream)}
.pill{position:absolute;border-radius:18px;font-weight:600;font-size:17px;letter-spacing:-0.8px;text-align:center;white-space:nowrap}
.pill-steps{left:112px;top:638px;width:227px;height:34px;line-height:34px;background:var(--purple);color:#fff}
.pill-elig{left:446px;top:641px;width:338px;height:36px;line-height:36px;background:var(--yellow);color:var(--navy)}
.steps-lead{position:absolute;left:102px;top:684px;font-size:17px;letter-spacing:-0.5px;color:var(--navy)}
.step-icon{position:absolute;width:78px;height:64px;border-radius:50%;background:var(--lavender-2)}
.step-num{position:absolute;width:25px;height:25px;border-radius:50%;background:var(--purple);color:#fff;font-size:15px;font-weight:600;text-align:center;line-height:25px}
.step-text{position:absolute;left:204px;width:192px;font-size:13.5px;line-height:17.6px;letter-spacing:-0.5px;color:var(--navy)}
.step-text b{font-weight:600}
.divider{position:absolute;border-top:1.5px dotted #b9a6d8}
.elig-icon{position:absolute;left:457px;width:74px;height:74px;border-radius:50%;background:var(--yellow)}
.elig-text{position:absolute;left:550px;width:200px;font-family:"Varela Round",sans-serif;font-size:15px;line-height:18px;letter-spacing:0.4px;color:var(--navy)}
.elig-divider{position:absolute;left:458px;width:315px;border-top:1.5px dotted #e6c55e}
.contact-band{position:absolute;left:57px;top:1008px}
.contact-q{position:absolute;left:226px;top:1025px;white-space:nowrap;font-size:17.5px;line-height:26px;color:#fff;letter-spacing:-0.3px}
.contact-q .second{letter-spacing:-0.9px}
.contact-q .hand{font-family:"Caveat",cursive;font-weight:700;font-size:24px;color:var(--yellow);letter-spacing:0;margin-left:6px}
.email{position:absolute;left:220px;top:1090px;width:330px;height:45px;border-radius:23px;background:#fff;text-align:center;line-height:45px;
  font-family:"Montserrat",sans-serif;font-weight:700;font-size:22px;color:var(--navy);white-space:nowrap}
.comp{position:absolute;left:598px;top:992px;width:172px;height:160px;border-radius:50%;background:var(--lavender-2);transform:rotate(-6deg)}
.comp-text{position:absolute;left:612px;top:1077px;width:150px;text-align:center;font-family:"Montserrat",sans-serif;font-weight:700;font-size:14.5px;line-height:20px;letter-spacing:0.6px;color:var(--navy);transform:rotate(6deg)}
.footer-names{position:absolute;left:265px;top:1150px;font-size:12px;letter-spacing:3px;color:#fff;white-space:nowrap}
.footer-names span{margin-left:24px}
</style>
</head>
<body>
<main class="flyer">
  <svg class="bg-wash" width="848" height="1200" viewBox="0 0 848 1200" aria-hidden="true">
    <path d="M0 0 H848 V60 C700 40 600 20 470 0 Z" fill="#dfe9fb"/>
    <path d="M0 0 C60 20 30 200 0 340 Z" fill="#ead9fb"/>
    <path d="M520 110 C600 40 760 40 848 70 V470 H500 C470 330 450 200 520 110 Z" fill="#d4bff3"/>
    <circle cx="770" cy="300" r="95" fill="var(--yellow)"/>
    <path d="M470 470 C560 430 700 420 848 440 V480 H470 Z" fill="#7fa2e8"/>
  </svg>

  <div class="hero-photo" role="img" aria-label="Photo of a thoughtful teenage girl in a lavender sweatshirt resting her chin on her hand"></div>

  <svg class="deco" width="848" height="480" viewBox="0 0 848 480" aria-hidden="true">
    <g stroke="var(--navy)" stroke-width="3" stroke-linecap="round" fill="none">
      <path d="M82 105 L72 95"/><path d="M75 125 L60 120"/><path d="M75 145 L58 145"/>
      <path d="M435 105 L445 92"/><path d="M440 125 L455 117"/><path d="M440 145 L458 145"/>
      <path d="M420 215 C450 240 445 275 410 275" stroke-width="2.5"/>
      <path d="M418 266 L408 276 L421 282" stroke-width="2.5"/>
    </g>
    <path d="M78 262 C140 252 300 250 405 256 L398 285 L408 318 C300 326 160 325 82 320 L90 290 Z" fill="var(--yellow)"/>
    <path d="M310 390 C370 385 420 387 452 392" stroke="var(--purple)" stroke-width="2.5" fill="none" stroke-linecap="round"/>
    <g fill="none" stroke="#fff" stroke-width="2">
      <path d="M800 75 l6 -6 a5 5 0 0 0 -8 -6 a5 5 0 0 0 -8 6 z"/>
      <path d="M786 115 l5 12 13 1 -10 8 3 13 -11 -7 -11 7 3 -13 -10 -8 13 -1z"/>
    </g>
    <ellipse cx="520" cy="92" rx="46" ry="38" fill="#fff" stroke="var(--navy)" stroke-width="2"/>
    <circle cx="520" cy="92" r="20" fill="none" stroke="var(--navy)" stroke-width="1.5"/>
    <circle cx="523" cy="145" r="6" fill="#fff" stroke="var(--navy)" stroke-width="2"/>
    <circle cx="535" cy="158" r="4" fill="#fff" stroke="var(--navy)" stroke-width="2"/>
  </svg>

  <div class="headline">
    <div class="h-are">Are you the</div>
    <div class="h-parent">parent</div>
    <div class="h-child">of a child</div>
    <div class="h-age">age 10-17?</div>
  </div>

  <p class="sub-q">Do they worry or <span class="hand">overthink</span><br>negative emotions?</p>

  <svg class="intro-band" width="848" height="170" viewBox="0 0 848 170" aria-hidden="true">
    <path d="M0 18 C220 0 600 10 848 0 V150 C600 165 300 150 30 165 L0 155 Z" fill="var(--navy)"/>
    <g stroke="#fff" stroke-width="2.5" stroke-linecap="round"><path d="M95 42 L105 55"/><path d="M80 60 L95 65"/><path d="M84 80 L97 80"/></g>
  </svg>
  <div class="brain-art" role="img" aria-label="Illustration of a brain with a heart"></div>
  <p class="intro-text">Northvale University researchers are seeking <strong>girls age 10-17</strong> for a study about brain activity in emotions and decision-making and how they relate to puberty, anxiety and depression.</p>

  <section class="panel panel-steps"></section>
  <div class="pill pill-steps">STUDY PARTICIPATION</div>
  <p class="steps-lead">Study participation involves</p>

  <div class="step-icon" style="left:77px;top:713px"></div>
  <div class="step-icon" style="left:77px;top:795px"></div>
  <div class="step-icon" style="left:77px;top:882px;height:80px"></div>
  <div class="elig-icon" style="top:699px"></div>
  <div class="elig-icon" style="top:791px"></div>
  <div class="elig-icon" style="top:881px"></div>

  <svg class="deco" width="848" height="1000" viewBox="0 0 848 1000" aria-hidden="true">
    <rect x="103" y="724" width="28" height="22" rx="10" fill="var(--purple)"/>
    <rect x="118" y="738" width="18" height="14" rx="7" fill="#fff"/>
    <g stroke="#fff" stroke-width="2"><path d="M111 733 H124"/><path d="M111 738 H121"/></g>
    <rect x="101" y="805" width="30" height="38" rx="3" fill="#fff" stroke="var(--navy)" stroke-width="2"/>
    <rect x="109" y="802" width="14" height="6" rx="2" fill="var(--navy)"/>
    <g stroke="var(--navy)" stroke-width="1.5"><path d="M106 815 H126"/><path d="M106 821 H126"/><path d="M106 827 H126"/><path d="M106 833 H120"/></g>
    <circle cx="116" cy="912" r="17" fill="#fff" stroke="var(--navy)" stroke-width="3"/>
    <circle cx="116" cy="912" r="8" fill="var(--navy)"/>
    <rect x="98" y="922" width="36" height="12" rx="3" fill="var(--navy)"/>
    <rect x="476" y="718" width="36" height="34" rx="5" fill="#fff" stroke="var(--navy)" stroke-width="2.5"/>
    <path d="M476 727 H512" stroke="var(--navy)" stroke-width="2.5"/>
    <g fill="var(--navy)"><rect x="482" y="733" width="6" height="5"/><rect x="491" y="733" width="6" height="5"/><rect x="500" y="733" width="6" height="5"/><rect x="482" y="742" width="6" height="5"/><rect x="491" y="742" width="6" height="5"/><rect x="500" y="742" width="6" height="5"/></g>
    <path d="M478 838 C470 820 490 810 498 818 C504 806 524 810 522 824 C536 824 534 844 520 844 H488 C478 844 474 842 478 838 Z" fill="#fff" stroke="var(--navy)" stroke-width="2"/>
    <circle cx="482" cy="854" r="4" fill="#fff" stroke="var(--navy)" stroke-width="2"/>
    <path d="M477 904 L494 896 L511 904 V920 C511 932 502 940 494 943 C486 940 477 932 477 920 Z" fill="var(--purple)" stroke="var(--navy)" stroke-width="2"/>
    <path d="M486 920 L492 926 L503 913" stroke="#fff" stroke-width="3" fill="none" stroke-linecap="round"/>
  </svg>

  <div class="step-num" style="left:168px;top:723px">1</div>
  <p class="step-text" style="top:721px"><b>One one-hour interview</b> (online or in-person) where your child will discuss their thoughts</p>
  <div class="divider" style="left:82px;top:788px;width:310px"></div>
  <div class="step-num" style="left:168px;top:805px">2</div>
  <p class="step-text" style="top:808px"><b>Online questionnaires</b><br>(parent and child)</p>
  <div class="divider" style="left:82px;top:865px;width:310px"></div>
  <div class="step-num" style="left:168px;top:881px">3</div>
  <p class="step-text" style="top:874px"><b>One two-hour visit</b> where your child will complete an MRI scan, answer questions about their puberty stage, and have a small hair sample taken to study puberty hormones</p>

  <section class="panel panel-elig" style="z-index:-1"></section>
  <div class="pill pill-elig">YOUR CHILD MAY BE ELIGIBLE IF THEY:</div>
  <p class="elig-text" style="top:729px">Are age 10-17</p>
  <div class="elig-divider" style="top:782px"></div>
  <p class="elig-text" style="top:806px">Tend to worry or overthink negative thoughts</p>
  <div class="elig-divider" style="top:872px"></div>
  <p class="elig-text" style="top:893px">have not been diagnosed with psychosis, learning problems, or autism</p>

  <svg class="contact-band" width="745" height="172" viewBox="0 0 745 172" aria-hidden="true">
    <path d="M18 6 C250 0 500 8 730 2 C745 40 742 120 735 165 C500 172 250 168 20 170 C0 120 2 50 18 6 Z" fill="var(--navy)"/>
    <g stroke="var(--yellow)" stroke-width="3" stroke-linecap="round"><path d="M58 22 L66 38"/><path d="M38 42 L54 48"/><path d="M36 66 L52 64"/><path d="M722 60 L708 66"/><path d="M724 82 L708 80"/></g>
    <g transform="translate(70 45) rotate(-14)" fill="none" stroke="#fff" stroke-width="4" stroke-linejoin="round">
      <rect x="0" y="0" width="72" height="50" rx="4"/>
      <path d="M0 2 L36 30 L72 2"/><path d="M0 48 L27 24"/><path d="M72 48 L45 24"/>
    </g>
    <path d="M360 72 C420 66 480 64 520 66" stroke="var(--yellow)" stroke-width="2" fill="none"/>
  </svg>
  <p class="contact-q">Interested in participating?<br><span class="second">Want more information?</span><span class="hand">Please contact us!</span></p>
  <div class="email">solvestudy@nvhealth.org</div>

  <div class="comp"></div>
  <svg class="deco" width="848" height="1200" viewBox="0 0 848 1200" aria-hidden="true">
    <rect x="667" y="1033" width="44" height="12" rx="2" fill="var(--navy)"/>
    <rect x="671" y="1045" width="36" height="24" fill="var(--navy)"/>
    <rect x="686" y="1033" width="6" height="36" fill="var(--lavender-2)"/>
    <path d="M689 1033 C680 1018 668 1024 674 1033 M689 1033 C698 1018 710 1024 704 1033" stroke="var(--navy)" stroke-width="4" fill="none"/>
  </svg>
  <p class="comp-text">COMPENSATION<br>UP TO $140</p>

  <p class="footer-names">NORTHVALE UNIVERSITY<span>NVHEALTH</span></p>
</main>
</body>
</html>
```